Copper lark buildworks

Copper lark buildworks is a small construction company.
Who is a licenced builder, Carpenter, joiner,
working on heritage ,new build, speacial projects and sometimes furniture

Industry/Entity Type

Construction

```html
<!DOCTYPE html>
<html lang="en">
<head>
<meta charset="utf-8">
<title>Copper lark buildworks – Business Card</title>
<link rel="stylesheet" href="https://fonts.googleapis.com/css2?family=Montserrat:wght@400;500;700&display=swap">
<style>
  :root {
    --page-bg: #e9e9e6;
    --card-black: #0b0b0b;
    --card-charcoal: #1c1c1c;
    --accent-bright: #5ea12e;
    --accent-muted: #5a8a3c;
    --name-green: #8fd46a;
    --text-light: #f2f2f2;
    --divider: #9a9a9a;
  }
  * { margin: 0; padding: 0; box-sizing: border-box; }
  html, body {
    width: 1200px; height: 1000px; overflow: hidden;
    background: var(--page-bg);
    font-family: "Montserrat", Arial, sans-serif;
  }
  .business-card {
    position: absolute; left: 150px; top: 240px;
    width: 900px; height: 520px;
    border-radius: 34px; overflow: hidden;
    background: radial-gradient(ellipse at 45% 30%, var(--card-charcoal) 0%, var(--card-black) 70%);
    box-shadow: 0 12px 30px rgba(0,0,0,0.25);
  }
  .card-wave { position: absolute; inset: 0; width: 900px; height: 520px; }
  .identity {
    position: absolute; left: 120px; top: 186px; width: 310px;
    text-align: center;
  }
  .identity-name {
    color: var(--name-green); font-weight: 700; font-size: 34px; line-height: 1.1;
  }
  .identity-role {
    color: var(--text-light); font-weight: 400; font-size: 19px; margin-top: 4px;
  }
  .divider {
    position: absolute; left: 450px; top: 132px; width: 1.5px; height: 176px;
    background: var(--divider);
  }
  .contact-list {
    position: absolute; left: 476px; top: 140px;
    list-style: none; color: var(--text-light); font-size: 19px; line-height: 31px;
  }
  .contact-list li { display: flex; align-items: center; gap: 10px; }
  .contact-icon { width: 22px; height: 22px; flex: none; }
</style>
</head>
<body>
  <section class="business-card" aria-label="Copper lark buildworks business card">
    <svg class="card-wave" viewBox="0 0 900 520" aria-hidden="true">
      <path d="M0,462 C220,420 360,350 560,345 C730,340 840,300 900,180 L900,520 L0,520 Z" fill="var(--accent-bright)"/>
      <path d="M0,486 C220,446 370,374 570,369 C740,364 850,326 900,214 L900,520 L0,520 Z" fill="var(--accent-muted)" stroke="#000" stroke-width="4"/>
    </svg>

    <div class="identity">
      <p class="identity-name">Owen Harlow</p>
      <p class="identity-role">Licenced Builder &amp; Carpenter</p>
    </div>

    <div class="divider"></div>

    <ul class="contact-list">
      <li>Your Street Address Here</li>
      <li>Singapore 56789</li>
      <li>
        <svg class="contact-icon" viewBox="0 0 22 22" aria-label="Phone"><circle cx="11" cy="11" r="10" fill="var(--accent-bright)"/><path d="M6,9 Q11,5 16,9 L15,11 L13,10 L13,9 Q11,8 9,9 L9,10 L7,11 Z M7,12 H15 V16 H7 Z" fill="#111"/></svg>
        0431627509
      </li>
      <li>
        <svg class="contact-icon" viewBox="0 0 22 22" aria-label="Email"><circle cx="11" cy="11" r="10" fill="var(--accent-bright)"/><rect x="5.5" y="7" width="11" height="8" fill="none" stroke="#111" stroke-width="1.5"/><path d="M5.5,7 L11,12 L16.5,7" fill="none" stroke="#111" stroke-width="1.5"/></svg>
        owen@copperlark.com
      </li>
      <li>
        <svg class="contact-icon" viewBox="0 0 22 22" aria-label="Website"><circle cx="11" cy="11" r="10" fill="var(--accent-bright)"/><circle cx="11" cy="11" r="6" fill="none" stroke="#111" stroke-width="1.4"/><ellipse cx="11" cy="11" rx="2.6" ry="6" fill="none" stroke="#111" stroke-width="1.2"/><path d="M5,11 H17" stroke="#111" stroke-width="1.2"/></svg>
        www.copperlark.com
      </li>
    </ul>
  </section>
</body>
</html>
```